Smile club flyer design

I am launching an office smile club and would like a design that sits my branding and that is appealing to customers. I have a design (I need a new one) that has all the information.
My website is maplehavendentalcarekx.com
Brand color is green. The design can be any color

Target Market(s)

Ages 30+

Industry/Entity Type

Dental

Font styles to use
Serif

Requirements
Must have
• Appealing to patients

```html
<!DOCTYPE html>
<html lang="en">
<head>
<meta charset="utf-8">
<title>Smile Club Membership Flyer</title>
<link href="https://fonts.googleapis.com/css2?family=EB+Garamond:wght@600;700&family=Montserrat:wght@500;600;700;800&family=Poppins:wght@500;600&family=Roboto+Condensed:wght@600&family=Yellowtail&display=swap" rel="stylesheet">
<style>
  :root{
    --stage:#3a3a3a;
    --brand:#1f7f44;
    --brand-dark:#0f4a26;
    --bg-top:#d6efdc;
    --bg-mid:#b9e3c5;
    --bg-low:#a7d9b9;
    --core-head:#80d288;
    --core-price:#5fb868;
    --core-body:#bdedc9;
    --core-line:#7fcf89;
    --bright-head:#047a6f;
    --bright-price:#03978b;
    --bright-body:#63d3c4;
    --bright-line:#0b6b61;
    --total-head:#00cfcc;
    --total-price:#00b8ba;
    --total-body:#58e8ec;
    --total-line:#12cfd1;
    --refresh-head:#a3d693;
    --refresh-price:#7bba6b;
    --refresh-body:#d0eccb;
    --refresh-line:#1d5a2e;
    --orange:#ee8412;
    --ink:#2a2f2c;
    --navy:#15223a;
    --list-ink:#1d4d2b;
  }
  *{box-sizing:border-box;margin:0;padding:0}
  html,body{width:1011px;height:1200px;overflow:hidden}
  body{background:var(--stage);position:relative;font-family:'Montserrat',sans-serif}
  .flyer{position:absolute;left:173px;top:101px;width:665px;height:997px;overflow:hidden;
    background:linear-gradient(180deg,var(--bg-top) 0%,var(--bg-mid) 55%,var(--bg-low) 100%)}
  .abs{position:absolute}
  .hero-photo{left:171px;top:0;width:340px;height:158px;
    background:radial-gradient(ellipse at 50% 45%,#f1c7ad 0%,#d98a5e 40%,#a8542c 62%,rgba(190,225,200,0) 78%)}
  .intro{left:58px;top:60px;font-family:'Yellowtail',cursive;font-size:42px;color:var(--brand-dark)}
  .brand{left:420px;top:38px;width:232px;text-align:center;font-family:'EB Garamond',serif;font-weight:700;color:var(--brand)}
  .brand-name{font-size:42px;line-height:1}
  .brand-sub{font-size:14px;letter-spacing:5px;margin-top:2px}
  .club-banner{left:58px;top:157px;width:549px;height:105px;background:var(--brand);
    border-radius:22px 48px 22px 48px;display:flex;align-items:center;justify-content:center}
  .club-title{font-weight:800;font-size:78px;color:#fff;letter-spacing:-1px;line-height:1}
  .membership{left:0;top:272px;width:665px;text-align:center;font-weight:800;font-size:50px;color:var(--brand);line-height:1}
  .tagline{left:0;top:332px;width:665px;text-align:center;font-family:'Poppins',sans-serif;font-weight:600;font-size:15px;color:var(--ink)}
  .plan{position:absolute;top:371px;width:183px;height:295px}
  .plan-body{position:absolute;left:5px;right:5px;top:118px;bottom:0;border:2px solid;border-top:none;border-radius:0 0 14px 14px;
    box-shadow:0 0 10px rgba(255,255,255,.7)}
  .plan-head{position:absolute;left:0;top:0;width:183px;height:152px}
  .plan-text{position:absolute;left:0;top:0;width:183px;text-align:center;color:#fff}
  .plan-name{margin-top:20px;font-weight:800;font-size:22px;line-height:1}
  .plan-kind{font-weight:500;font-size:15px;margin-top:4px}
  .price-box{position:absolute;left:22px;top:70px;width:139px;height:56px;border-radius:8px;text-align:center;color:#fff}
  .price{font-weight:800;font-size:37px;line-height:1;margin-top:6px;text-shadow:0 2px 3px rgba(0,0,0,.3)}
  .per{font-weight:500;font-size:12px;line-height:1;margin-top:-3px}
  .perks{position:absolute;left:18px;right:6px;list-style:none;font-family:'Roboto Condensed',sans-serif;font-weight:600;font-size:10.5px;line-height:1.25}
  .perks li{position:relative;padding-left:13px;margin-bottom:9px}
  .perks svg{position:absolute;left:0;top:1px;width:10px;height:10px}
  .core{left:42px}.bright{left:245px}.total{left:448px}
  .core .plan-body{background:var(--core-body);border-color:var(--core-line)}
  .core .price-box{background:var(--core-price)}
  .core .perks{top:183px;color:var(--list-ink)}
  .bright .plan-body{background:var(--bright-body);border-color:var(--bright-line)}
  .bright .price-box{background:var(--bright-price)}
  .bright .perks{top:183px;color:#0d4d45}
  .total .plan-body{background:var(--total-body);border-color:var(--total-line)}
  .total .price-box{background:var(--total-price)}
  .total .perks{top:172px;color:#0b4a4d}
  .join-band{left:0;top:695px;width:665px;height:128px;background:#fff}
  .join-title{left:42px;top:716px;font-family:'EB Garamond',serif;font-weight:700;font-size:42px;color:var(--brand-dark);line-height:1}
  .join-phone{left:72px;top:760px;font-family:'EB Garamond',serif;font-weight:700;font-size:48px;color:var(--orange);line-height:1;letter-spacing:-1px}
  .refresh{left:449px;top:688px;height:296px}
  .refresh .plan-body{top:118px;background:var(--refresh-body);border-color:var(--refresh-line)}
  .refresh .plan-text{color:var(--brand-dark)}
  .refresh .plan-name{margin-top:19px;font-size:22px}
  .refresh .plan-kind{font-size:15px;margin-top:3px;color:var(--brand-dark)}
  .refresh .price-box{top:64px;height:56px;background:var(--refresh-price)}
  .refresh .price{font-size:38px;margin-top:9px}
  .refresh .perks{top:160px;left:26px;font-size:13px;color:var(--brand-dark)}
  .refresh .perks li{padding-left:14px;margin-bottom:6px}
  .refresh .perks svg{top:3px}
  .offer{position:absolute;left:0;top:232px;width:183px;text-align:center;font-family:'EB Garamond',serif;font-weight:700;font-size:27px;line-height:1;color:var(--brand-dark)}
  .finance{left:22px;top:853px;font-family:'Poppins',sans-serif;font-weight:600;font-size:19.5px;color:var(--ink)}
  .partner{left:88px;top:887px;display:flex;align-items:center;gap:10px}
  .partner-dot{width:46px;height:46px;border-radius:50%;background:var(--navy)}
  .partner-name{font-family:'Poppins',sans-serif;font-weight:600;font-size:34px;color:var(--navy);line-height:1}
  .fee{left:37px;top:951px;font-family:'Poppins',sans-serif;font-weight:500;font-size:14px;color:var(--brand-dark)}
</style>
</head>
<body>
<svg width="0" height="0" style="position:absolute">
  <symbol id="tick" viewBox="0 0 10 10"><circle cx="5" cy="5" r="5" fill="currentColor"/><path d="M2.6 5.1 4.3 6.7 7.4 3.5" fill="none" stroke="#fff" stroke-width="1.4" stroke-linecap="round" stroke-linejoin="round"/></symbol>
</svg>
<main class="flyer">
  <div class="abs hero-photo" role="img" aria-label="Photo of a smiling red-haired woman pointing at her smile"></div>
  <div class="abs intro">Introducing</div>
  <div class="abs brand"><div class="brand-name">Maplehaven</div><div class="brand-sub">DENTAL CARE</div></div>
  <div class="abs club-banner"><span class="club-title">SMILE CLUB</span></div>
  <div class="abs membership">MEMBERSHIP</div>
  <div class="abs tagline">NO INSURANCE? NO PROBLEM</div>

  <section class="plan core">
    <div class="plan-body"></div>
    <svg class="plan-head" viewBox="0 0 183 152"><path d="M0 10Q0 0 10 0H173Q183 0 183 10V134L91.5 152 0 134Z" fill="var(--core-head)"/></svg>
    <div class="plan-text"><div class="plan-name">CORE CARE</div><div class="plan-kind">PREVENTIVE</div></div>
    <div class="price-box"><div class="price">$39</div><div class="per">/MONTH</div></div>
    <ul class="perks" style="color:var(--list-ink)">
      <li><svg style="color:#3aa35a"><use href="#tick"/></svg>Comprehensive Annual Exam</li>
      <li><svg style="color:#3aa35a"><use href="#tick"/></svg>2 Professional Cleanings per Year</li>
      <li><svg style="color:#3aa35a"><use href="#tick"/></svg>Routine Bitewing X-rays</li>
      <li><svg style="color:#3aa35a"><use href="#tick"/></svg>10% Savings on Treatment</li>
    </ul>
  </section>

  <section class="plan bright">
    <div class="plan-body"></div>
    <svg class="plan-head" viewBox="0 0 183 152"><path d="M0 10Q0 0 10 0H173Q183 0 183 10V134L91.5 152 0 134Z" fill="var(--bright-head)"/></svg>
    <div class="plan-text"><div class="plan-name">BRIGHT</div><div class="plan-kind">COSMETIC</div></div>
    <div class="price-box"><div class="price">$59</div><div class="per">/MONTH</div></div>
    <ul class="perks">
      <li><svg style="color:#0d7f72"><use href="#tick"/></svg>Annual In-Office Whitening (Top &amp; Bottom)</li>
      <li><svg style="color:#0d7f72"><use href="#tick"/></svg>Custom Whitening Trays</li>
      <li><svg style="color:#0d7f72"><use href="#tick"/></svg>15% Savings on Elective Treatment</li>
    </ul>
  </section>

  <section class="plan total">
    <div class="plan-body"></div>
    <svg class="plan-head" viewBox="0 0 183 152"><path d="M0 10Q0 0 10 0H173Q183 0 183 10V134L91.5 152 0 134Z" fill="var(--total-head)"/></svg>
    <div class="plan-text"><div class="plan-name">TOTAL SMILE</div><div class="plan-kind">PERIODONTAL</div></div>
    <div class="price-box"><div class="price">$89</div><div class="per">/MONTH</div></div>
    <ul class="perks">
      <li><svg style="color:#0a9ea0"><use href="#tick"/></svg>3-4 Perio Maintenance Visits per Year</li>
      <li><svg style="color:#0a9ea0"><use href="#tick"/></svg>1 Comprehensive Exam</li>
      <li><svg style="color:#0a9ea0"><use href="#tick"/></svg>Diagnostic X-rays</li>
      <li><svg style="color:#0a9ea0"><use href="#tick"/></svg>15% Savings on Restorative &amp; Elective Care</li>
    </ul>
  </section>

  <div class="abs join-band"></div>
  <div class="abs join-title">Join Smile Club Today!</div>
  <div class="abs join-phone">555-014-2370</div>

  <section class="plan refresh">
    <div class="plan-body"></div>
    <svg class="plan-head" viewBox="0 0 183 152"><path d="M0 10Q0 0 10 0H173Q183 0 183 10V134L91.5 152 0 134Z" fill="var(--refresh-head)"/></svg>
    <div class="plan-text"><div class="plan-name">SMILE</div><div class="plan-kind">REFRESH PACKAGE</div></div>
    <div class="price-box"><div class="price">$499</div></div>
    <ul class="perks">
      <li><svg style="color:var(--orange)"><use href="#tick"/></svg>Cleaning</li>
      <li><svg style="color:var(--orange)"><use href="#tick"/></svg>Comprehensive Exam</li>
      <li><svg style="color:var(--orange)"><use href="#tick"/></svg>Whitening</li>
    </ul>
    <div class="offer">Limited<br>Time Offer</div>
  </section>

  <div class="abs finance">FLEXIBLE FINANCING FOR TREATMENT</div>
  <div class="abs partner"><span class="partner-dot"></span><span class="partner-name">Plumline</span></div>
  <div class="abs fee">*$49 Lifetime Activation Fee (Non-Refundable)</div>
</main>
</body>
</html>
```